A website for a Maltese Law Firm

Our law firm needs a website to further its business. The site should have a simple yet effective design. We would need the following sections: About us, Practice Areas, About Malta, Contact. These should be further split as follows:

About us: Our firm, Our values, What others say, Offices

Practice Areas: Crimimal, Citizenship & Residence, Sovereign Patron Pathway, Criminal Defence, Civil Litigation, Arbitration and ADR, Commercial and Corporate, Media Law.

About Malta: just one section.

Contact: Just one section

We would also need a news feed at the front of the site to include latest news regarding our cases.

At the bottom we need a section for our Terms and a Privacy Statement.

Our logo is being attached.

Target Market(s)

All clients looking for legal assistance in Malta

Industry/Entity Type

Legal

Coding

Coded - Design and coding required

Number of Pages Required

1 page

Requirements
Must have
• It must be simple yet striking.

```html
<!DOCTYPE html>
<html lang="en">
<head>
<meta charset="utf-8">
<title>CM Advocates – Law Firm in Malta</title>
<link href="https://fonts.googleapis.com/css2?family=Raleway:wght@400;500;600;700&family=Open+Sans:ital,wght@0,400;0,600;0,700;1,400&display=swap" rel="stylesheet">
<style>
:root{
  --orange:#f5a100;
  --brown:#3c2218;
  --ink:#222222;
  --text:#555555;
  --muted:#777777;
  --line:#e4e4e4;
  --grey-band:#ececec;
  --white:#ffffff;
}
*{margin:0;padding:0;box-sizing:border-box}
html,body{width:1200px;height:2532px;overflow:hidden;background:var(--white)}
body{position:relative;font-family:"Open Sans",Arial,sans-serif;color:var(--text)}
.abs{position:absolute}
h1,h2,h3,h4,.raleway{font-family:"Raleway",Arial,sans-serif}
.lines{white-space:nowrap}

/* header */
.top-rule{left:0;top:0;width:1200px;height:5px;background:var(--brown)}
.site-header{left:0;top:5px;width:1200px;height:99px;background:var(--white)}
.brand{left:162px;top:30px;display:flex;align-items:center;gap:10px;font-family:"Raleway",sans-serif;font-weight:700;font-size:21px;color:var(--brown);letter-spacing:.3px}
.brand-mark{width:12px;height:12px;background:var(--brown)}
.callus{left:822px;top:17px;display:flex;align-items:center;gap:10px;font-family:"Raleway",sans-serif;font-weight:700;font-size:15px;color:var(--ink)}
.callus .dot{width:27px;height:27px;border-radius:50%;background:var(--orange);display:flex;align-items:center;justify-content:center}
.main-nav{left:494px;top:71px;font-family:"Raleway",sans-serif;font-weight:700;font-size:12.5px;color:var(--ink)}
.main-nav a{position:absolute;white-space:nowrap;text-decoration:none;color:inherit;top:0}
.main-nav a.active{color:var(--orange)}

/* hero */
.hero{left:0;top:104px;width:1200px;height:497px;background:linear-gradient(90deg,#2c1c14 0%,#4a2a22 35%,#3b2620 60%,#5a2520 100%)}
.hero-shade{left:0;top:0;width:100%;height:100%;background:radial-gradient(ellipse at 50% 40%,rgba(255,255,255,.08),rgba(0,0,0,.35))}
.hero-title{left:0;top:168px;width:1200px;text-align:center;font-weight:600;font-size:46px;color:var(--white);letter-spacing:1px}
.hero-sub{left:0;top:230px;width:1200px;text-align:center;font-family:"Raleway",sans-serif;font-weight:600;font-size:20px;line-height:27px;color:var(--white)}
.btn{display:flex;align-items:center;justify-content:center;background:var(--orange);color:var(--white);font-family:"Raleway",sans-serif;font-weight:700;text-transform:uppercase}
.hero-btn{left:506px;top:301px;width:188px;height:45px;font-size:15px;border:1px solid rgba(255,255,255,.6)}
.hero-arrow{top:231px;width:33px;height:33px}

/* section headings */
.section-title{display:flex;align-items:center;justify-content:center;gap:10px;font-weight:700;font-size:24px;color:var(--ink);text-transform:uppercase}
.bubble{width:33px;height:27px;flex:none}

/* practice areas */
.areas-title{left:0;top:634px;width:1200px}
.areas-intro{left:0;top:684px;width:1200px;text-align:center;font-size:10px;line-height:19px;color:#444}
.area{width:230px;text-align:center}
.area svg{display:block;margin:0 auto}
.area h3{font-weight:600;font-size:13.5px;color:var(--ink);margin-top:20px;line-height:18px}
.area p{font-size:10.5px;line-height:18px;color:var(--muted);margin-top:10px}
.v-divider{width:1px;background:var(--line)}
.h-divider{height:1px;background:var(--line)}

/* welcome */
.welcome{left:0;top:1187px;width:1200px;height:365px;background:var(--grey-band)}
.welcome-photo{left:162px;top:65px;width:351px;height:243px;border:4px solid var(--white);background:linear-gradient(135deg,#c9c3b6 0%,#5a6a80 45%,#1e2738 100%)}
.welcome-title{left:545px;top:66px;justify-content:flex-start}
.welcome-text{left:545px;top:116px;font-size:10px;line-height:20.8px;color:#444}
.welcome-btn{left:545px;top:269px;width:117px;height:38px;font-size:11.5px}

/* blog */
.blog-title{left:0;top:1586px;width:1200px}
.post{top:1638px;width:275px}
.post-photo{width:275px;height:162px;border:3px solid var(--white);box-shadow:0 0 0 1px var(--line)}
.post-date{margin-top:14px;font-weight:700;font-size:12px;color:var(--orange);display:flex;align-items:center;gap:6px}
.post h4{margin-top:10px;font-weight:600;font-size:16.5px;color:var(--ink)}
.post p{margin-top:8px;font-size:10px;line-height:17px;color:#444;white-space:nowrap}

/* evaluation */
.evaluation{left:0;top:1962px;width:1200px;height:252px;background:linear-gradient(180deg,#f6a51c 0%,#f39800 60%,#ee8a00 100%)}
.eval-title{left:0;top:45px;width:1200px;color:var(--white);font-size:21px}
.field{background:var(--white);border-radius:2px;font-size:10px;font-style:italic;color:#444;padding:10px 12px}
.submit{width:107px;height:28px;background:var(--brown);font-size:11px}

/* footer */
.site-footer{left:0;top:2214px;width:1200px;height:318px;background:var(--brown)}
.foot-col{top:48px;color:var(--white)}
.foot-col h4{font-weight:700;font-size:14px;text-transform:uppercase;margin-bottom:20px}
.foot-col li{list-style:none;font-size:11px;line-height:22.5px;white-space:nowrap}
.foot-col p{font-size:11px;line-height:18px;white-space:nowrap}
.foot-col .more{display:block;margin-top:16px;font-family:"Raleway",sans-serif;font-weight:700;font-size:11px;color:var(--orange)}
.foot-rule{left:162px;top:228px;width:876px;height:1px;background:#5a3a2d}
.copyright{left:162px;top:263px;font-size:10.5px;color:var(--white)}
.social{top:256px;width:27px;height:27px;border-radius:50%;background:#7a5a4b;border:1px solid #9a7a6a}
</style>
</head>
<body>

<div class="abs top-rule"></div>
<header class="abs site-header">
  <div class="abs brand" style="top:25px"><span class="brand-mark"></span>Calleja &amp; Mifsud Advocates</div>
  <div class="abs callus">
    <span class="dot"><svg width="14" height="14" viewBox="0 0 24 24"><path d="M6.6 10.8c1.4 2.8 3.8 5.1 6.6 6.6l2.2-2.2c.3-.3.7-.4 1-.2 1.1.4 2.3.6 3.6.6.6 0 1 .4 1 1V20c0 .6-.4 1-1 1C10.6 21 3 13.4 3 4c0-.6.4-1 1-1h3.5c.6 0 1 .4 1 1 0 1.3.2 2.5.6 3.6.1.3 0 .7-.2 1z" fill="#fff"/></svg></span>
    CALLUS : (356) 2134 7788
  </div>
  <nav class="abs main-nav">
    <a class="active" style="left:0">HOME</a>
    <a style="left:82px">ABOUT US</a>
    <a style="left:189px">PRACTICE AREAS</a>
    <a style="left:336px">ABOUT MALTA</a>
    <a style="left:468px">CONTACT US</a>
  </nav>
</header>

<section class="abs hero" role="img" aria-label="Photograph of the firm's advocates standing together in a wood-panelled meeting room">
  <div class="abs hero-shade"></div>
  <h1 class="abs hero-title">CM ADVOCATES</h1>
  <p class="abs hero-sub">Sed ut perspiciatis unde omnis iste natus error sit volu<br>ptatem accusantium doloremque laudanti</p>
  <div class="abs btn hero-btn">Get Started Here</div>
  <svg class="abs hero-arrow" style="left:37px" viewBox="0 0 33 33"><circle cx="16.5" cy="16.5" r="15" fill="none" stroke="#fff" stroke-width="1.5"/><path d="M19 10l-6.5 6.5L19 23" fill="none" stroke="#fff" stroke-width="2"/></svg>
  <svg class="abs hero-arrow" style="left:1127px" viewBox="0 0 33 33"><circle cx="16.5" cy="16.5" r="15" fill="none" stroke="#fff" stroke-width="1.5"/><path d="M14 10l6.5 6.5L14 23" fill="none" stroke="#fff" stroke-width="2"/></svg>
</section>

<!-- practice areas -->
<h2 class="abs section-title areas-title">
  <svg class="bubble" viewBox="0 0 33 27"><rect x="0" y="0" width="24" height="19" fill="#f5a100"/><rect x="9" y="8" width="24" height="19" fill="#f7b733"/></svg>
  Our Practice Areas
</h2>
<p class="abs areas-intro lines">Lorem ipsum dolor sit amet, consectetur adipiscing elit, sed do eiusmod tempor incididunt ut labore et dolore magna aliqua. Ut enim ad minim veniam,<br>quis nostrud exercitation ullamco laboris nisi ut aliquip ex ea commodo consequat. Duis aute irure dolor in reprehenderit in voluptate velit ess</p>

<div class="abs v-divider" style="left:363px;top:752px;height:185px"></div>
<div class="abs v-divider" style="left:604px;top:752px;height:185px"></div>
<div class="abs v-divider" style="left:836px;top:752px;height:185px"></div>
<div class="abs v-divider" style="left:363px;top:962px;height:185px"></div>
<div class="abs v-divider" style="left:604px;top:962px;height:185px"></div>
<div class="abs v-divider" style="left:836px;top:962px;height:185px"></div>
<div class="abs h-divider" style="left:162px;top:948px;width:876px"></div>

<div class="abs area" style="left:133px;top:760px">
  <svg width="96" height="80" viewBox="0 0 96 80">
    <g fill="none" stroke="#f5a100" stroke-width="5">
      <circle cx="26" cy="44" r="15"/><circle cx="70" cy="54" r="15"/>
      <circle cx="43" cy="20" r="4" stroke-width="3"/><circle cx="52" cy="20" r="4" stroke-width="3"/>
    </g>
    <g fill="#f5a100"><rect x="27" y="22" width="12" height="10" rx="2"/><rect x="57" y="26" width="12" height="10" rx="2"/></g>
  </svg>
  <h3>Criminal</h3>
  <p>Sed ut perspiciatis unde omnis iste<br>natus error sit voluptatem accu.</p>
</div>
<div class="abs area" style="left:374px;top:760px">
  <svg width="100" height="80" viewBox="0 0 100 80"><path d="M32 52V32l18-15 18 15v20z" fill="#3c2218"/><path d="M24 33l26-22 26 22" fill="none" stroke="#3c2218" stroke-width="5" stroke-linejoin="round"/><path d="M6 58q11-8 22 0t22 0 22 0 22 0M12 70q10-7 20 0t20 0 20 0 16 0" fill="none" stroke="#3c2218" stroke-width="4"/></svg>
  <h3>Citizenship &amp; Residence</h3>
  <p>Sed ut perspiciatis unde omnis iste<br>natus error sit voluptatem accu.</p>
</div>
<div class="abs area" style="left:603px;top:760px">
  <svg width="90" height="80" viewBox="0 0 90 80"><g fill="#3c2218"><rect x="42" y="6" width="6" height="62"/><rect x="28" y="66" width="34" height="7"/><rect x="12" y="14" width="66" height="4"/><circle cx="45" cy="8" r="5"/><path d="M4 44h28a14 8 0 0 1-28 0zM58 44h28a14 8 0 0 1-28 0z"/></g><path d="M18 18L6 44M18 18l12 26M72 18L60 44M72 18l12 26" stroke="#3c2218" stroke-width="2" fill="none"/></svg>
  <h3>Criminal Defence</h3>
  <p>Sed ut perspiciatis unde omnis iste<br>natus error sit voluptatem accu.</p>
</div>
<div class="abs area" style="left:843px;top:760px">
  <svg width="100" height="80" viewBox="0 0 100 80"><g fill="#3c2218"><g transform="rotate(20 40 30)"><rect x="22" y="12" width="16" height="34" rx="3"/><rect x="38" y="24" width="56" height="9" rx="2"/></g><rect x="14" y="56" width="30" height="6"/><rect x="6" y="62" width="46" height="9"/></g></svg>
  <h3>Civil Litigation</h3>
  <p>Sed ut perspiciatis unde omnis iste<br>natus error sit voluptatem accu.</p>
</div>

<div class="abs area" style="left:133px;top:968px">
  <svg width="80" height="76" viewBox="0 0 80 76"><g fill="#3c2218"><rect x="10" y="6" width="56" height="16" rx="3"/><rect x="16" y="26" width="56" height="16" rx="3"/><rect x="8" y="46" width="62" height="22" rx="3"/></g><g fill="#fff"><rect x="18" y="12" width="46" height="4"/><rect x="24" y="32" width="46" height="4"/><rect x="16" y="54" width="52" height="5"/></g></svg>
  <h3>Arbitration and ADR</h3>
  <p>Sed ut perspiciatis unde omnis iste<br>natus error sit voluptatem accu.</p>
</div>
<div class="abs area" style="left:374px;top:968px">
  <svg width="80" height="76" viewBox="0 0 80 76"><g fill="#3c2218"><rect x="28" y="4" width="26" height="68"/><rect x="8" y="34" width="22" height="38"/><rect x="52" y="26" width="22" height="46"/></g><g fill="#fff"><rect x="34" y="12" width="5" height="6"/><rect x="43" y="12" width="5" height="6"/><rect x="34" y="24" width="5" height="6"/><rect x="43" y="24" width="5" height="6"/><rect x="34" y="36" width="5" height="6"/><rect x="43" y="36" width="5" height="6"/><rect x="13" y="42" width="5" height="6"/><rect x="58" y="34" width="5" height="6"/><rect x="58" y="46" width="5" height="6"/></g></svg>
  <h3>Commercial &amp; Corporate</h3>
  <p>Sed ut perspiciatis unde omnis iste<br>natus error sit voluptatem accu.</p>
</div>
<div class="abs area" style="left:603px;top:968px">
  <svg width="96" height="76" viewBox="0 0 96 76"><g fill="#3c2218"><g transform="rotate(-20 40 22)"><rect x="20" y="6" width="34" height="16" rx="3"/><rect x="33" y="22" width="8" height="30"/></g><rect x="14" y="54" width="56" height="7"/><rect x="6" y="62" width="72" height="9"/></g></svg>
  <h3>Media Law</h3>
  <p>Sed ut perspiciatis unde omnis iste<br>natus error sit voluptatem accu.</p>
</div>
<div class="abs area" style="left:843px;top:968px">
  <svg width="76" height="76" viewBox="0 0 76 76" role="img" aria-label="Icon of an individual investor"><g fill="#3c2218"><circle cx="38" cy="22" r="15"/><path d="M8 72c0-18 12-30 30-30s30 12 30 30z"/></g><path d="M33 44l5 6 5-6-5 24z" fill="#fff"/></svg>
  <h3>Sovereign Patron<br>Pathway</h3>
  <p>Sed ut perspiciatis unde omnis iste</p>
</div>

<!-- welcome -->
<section class="abs welcome">
  <div class="abs welcome-photo" role="img" aria-label="Photograph of a senior advocate with his team in an office"></div>
  <h2 class="abs section-title welcome-title">
    <svg class="bubble" viewBox="0 0 33 27"><rect x="0" y="0" width="24" height="19" fill="#f5a100"/><rect x="9" y="8" width="24" height="19" fill="#f7b733"/></svg>
    Welcome to our site!
  </h2>
  <p class="abs welcome-text lines">Lorem ipsum dolor sit amet, consectetur adipiscing elit, sed do eiusmod tempor incididunt ut labore<br>et dolore magna aliqua. Ut enim ad minim veniam, quis nostrud exercitation ullamco laboris nisi ut al<br>iquip ex ea commodo consequat. Duis aute irure dolor in reprehenderit in voluptate velit essLorem<br>ipsum dolor sit amet, consectetur adipiscing elit, sed do eiusmod tempor incididunt ut labore et dol<br>ore magna aliqua. Ut enim ad minim veniam, quis nostrud exercitation ullamco laboris nisi ut ali quip<br>ex ea commodo consequat. Duis aute irure dolor in reprehenderit in voluptate velit essLorem ipsum<br>dolor sit amet, consectetur adipiscing elit, sed do eiusmod tempor incididunt ut.</p>
  <div class="abs btn welcome-btn">Read More</div>
</section>

<!-- blog -->
<h2 class="abs section-title blog-title">
  <svg class="bubble" viewBox="0 0 33 27"><rect x="0" y="0" width="24" height="19" fill="#f5a100"/><rect x="9" y="8" width="24" height="19" fill="#f7b733"/></svg>
  Latest Blog News
</h2>

<article class="abs post" style="left:162px">
  <div class="post-photo" role="img" aria-label="Photograph of advocates reviewing a case file" style="background:linear-gradient(135deg,#d9d4cc 0%,#6b6660 50%,#2a2c36 100%)"></div>
  <div class="post-date raleway"><svg width="11" height="11" viewBox="0 0 11 11"><rect x=".5" y="1.5" width="10" height="9" fill="none" stroke="#f5a100"/><rect x=".5" y="1.5" width="10" height="3" fill="#f5a100"/></svg>June 08 , 2016</div>
  <h4>Finibus Bonorum et Malorum</h4>
  <p>Sed ut perspiciatis unde omnis iste natus error sitvolu<br>ptatem accusantium doloremque laudtatemed ut pe<br>rspiciatis unde omnis iste natuor situ ptate.</p>
</article>
<article class="abs post" style="left:462px">
  <div class="post-photo" role="img" aria-label="Photograph of a handshake between a lawyer and a client" style="background:linear-gradient(135deg,#e8eef4 0%,#8aa3bd 50%,#2c3e58 100%)"></div>
  <div class="post-date raleway"><svg width="11" height="11" viewBox="0 0 11 11"><rect x=".5" y="1.5" width="10" height="9" fill="none" stroke="#f5a100"/><rect x=".5" y="1.5" width="10" height="3" fill="#f5a100"/></svg>June 08 , 2016</div>
  <h4>Finibus Bonorum et Malorum</h4>
  <p>Sed ut perspiciatis unde omnis iste natus error sitvolu<br>ptatem accusantium doloremque laudtatemed ut pe<br>rspiciatis unde omnis iste natusr sitvolu ptate.</p>
</article>
<article class="abs post" style="left:764px">
  <div class="post-photo" role="img" aria-label="Photograph of two people signing a document" style="background:linear-gradient(135deg,#6e3a2a 0%,#3a2a26 50%,#161616 100%)"></div>
  <div class="post-date raleway"><svg width="11" height="11" viewBox="0 0 11 11"><rect x=".5" y="1.5" width="10" height="9" fill="none" stroke="#f5a100"/><rect x=".5" y="1.5" width="10" height="3" fill="#f5a100"/></svg>June 08 , 2016</div>
  <h4>Finibus Bonorum et Malorum</h4>
  <p>Sed ut perspiciatis unde omnis iste natus error sitvolu<br>ptatem accusantium doloremque laudtatemed ut pe<br>rspiciatis unde omnis iste natur sitvolu ptate.</p>
</article>

<!-- free case evaluation -->
<section class="abs evaluation">
  <h2 class="abs section-title eval-title">
    <svg class="bubble" viewBox="0 0 33 27"><rect x="0" y="0" width="24" height="19" fill="#ffffff"/><rect x="9" y="8" width="24" height="19" fill="#ffe3b0"/></svg>
    Free Case Evaluation
  </h2>
  <div class="abs field" style="left:263px;top:88px;width:219px;height:35px">Name:</div>
  <div class="abs field" style="left:490px;top:88px;width:219px;height:35px">Email:</div>
  <div class="abs field" style="left:717px;top:88px;width:218px;height:35px">Phone</div>
  <div class="abs field" style="left:263px;top:131px;width:672px;height:80px">Message:</div>
  <div class="abs btn submit" style="left:826px;top:178px">Submit Here</div>
</section>

<!-- footer -->
<footer class="abs site-footer">
  <div class="abs foot-col" style="left:162px">
    <h4 class="raleway">Company</h4>
    <ul><li>Home,</li><li>About us</li><li>Practice Areas</li><li>About Malta</li><li>Contact us</li></ul>
  </div>
  <div class="abs foot-col" style="left:291px">
    <h4 class="raleway">Practice Areas</h4>
    <ul><li>Crimimal,</li><li>Citizenship &amp; Residence,</li><li>Sovereign Patron Pathway,</li><li>Criminal Defence,</li><li>Civil Litigation</li></ul>
  </div>
  <div class="abs foot-col" style="left:538px">
    <h4 class="raleway">Terms and a Privacy</h4>
    <p>Sed ut perspiciatis unde omnis iste natus error<br>sit voluptatem accusantium doloremquelo lau<br>dant ium, totam rem aperiam, eaque ipsa qua<br>illo ium, totam rem aperiam, eainv</p>
    <span class="more">READ MORE</span>
  </div>
  <div class="abs foot-col" style="left:854px">
    <h4 class="raleway">Contact</h4>
    <ul><li>12/4, Harbour Lane, Valletta</li><li>9/2, Orchard Road, Birkirkara</li><li>Tel: (356)2134 7788, (356)2134 7790</li><li>Fax: (356)2134 7791</li><li>Email:info@cmadvocates.example</li></ul>
  </div>
  <div class="abs foot-rule"></div>
  <p class="abs copyright">© 2015 cmadvocates.example.&nbsp; All right reserved&nbsp; Term of Use</p>
  <span class="abs social" style="left:911px"></span>
  <span class="abs social" style="left:941px"></span>
  <span class="abs social" style="left:971px"></span>
  <span class="abs social" style="left:1001px"></span>
</footer>

</body>
</html>
```